Redesign of business card for Cedar Ridge Mechanical

We are looking for a new design for our business cards for Cedar Ridge Mechanical. We are a plumbing & HVAC construction company, operating on the West Coast of Canada and USA. Logo attached.
Industry/Entity Type
Construction - Plumbing & HVAC
Contact Information for Business Card
Name, address, phone numbers, email, website address
Look and feel
Each slider illustrates characteristics of the customer's brand and the style your logo design should communicate.

```html
<!DOCTYPE html>
<html lang="en">
<head>
<meta charset="utf-8">
<title>Cedar Ridge Mechanical – Business Card</title>
<link rel="stylesheet" href="https://fonts.googleapis.com/css2?family=Montserrat:wght@400;500;700&family=Questrial&display=swap">
<style>
  :root {
    --stage: #3b3b3d;
    --card-black: #1e1e1f;
    --card-white: #ffffff;
    --band-grey: #b9b9b9;
    --ink: #1c1c1c;
    --light-text: #f2f2f2;
    --silver: #d2d2d2;
    --divider: #6a6a6a;
  }
  * { box-sizing: border-box; margin: 0; padding: 0; }
  html, body {
    width: 1200px; height: 1200px; overflow: hidden;
    background: var(--stage);
  }
  .canvas {
    width: 1200px; height: 1200px;
    display: flex; flex-direction: column; align-items: center; justify-content: center;
    gap: 70px;
  }
  .card {
    width: 840px; height: 480px;
    border-radius: 38px;
    overflow: hidden;
    position: relative;
    box-shadow: 0 14px 30px rgba(0,0,0,0.35);
  }

  /* Front */
  .card-front { background: var(--card-black); }
  .front-top {
    position: absolute; inset: 0 0 auto 0; height: 236px;
    background: var(--card-white);
    display: flex; align-items: center; justify-content: center; gap: 18px;
  }
  .front-band {
    position: absolute; left: 0; right: 0; top: 236px; height: 12px;
    background: linear-gradient(to right, var(--band-grey), #e4e4e4 70%, #f5f5f5);
  }
  .brand-mark {
    width: 34px; height: 34px; border: 5px solid var(--ink);
  }
  .brand-name {
    font-family: "Montserrat", sans-serif; font-weight: 700;
    font-size: 34px; letter-spacing: 3px; text-transform: uppercase;
    color: var(--ink);
  }
  .front-bottom {
    position: absolute; left: 0; right: 0; top: 248px; bottom: 0;
    display: grid; grid-template-columns: 1fr 1px 1fr; align-items: center;
  }
  .identity { padding-left: 80px; padding-top: 50px; color: var(--light-text); }
  .identity-name {
    font-family: "Montserrat", sans-serif; font-weight: 700; font-size: 40px; line-height: 1;
  }
  .identity-role {
    font-family: "Montserrat", sans-serif; font-weight: 400; font-size: 24px; margin-top: 4px;
  }
  .divider { width: 1px; height: 150px; background: var(--divider); }
  .contact-list {
    list-style: none; padding-left: 44px; color: var(--light-text);
    font-family: "Questrial", sans-serif; font-size: 22px; line-height: 1.2;
  }
  .contact-list li { display: flex; align-items: flex-start; gap: 10px; }
  .contact-list svg { width: 20px; height: 20px; flex: none; margin-top: 3px; fill: var(--light-text); }

  /* Back */
  .card-back {
    background: var(--card-black);
    display: flex; align-items: center; justify-content: center; gap: 22px;
  }
  .card-back .brand-mark { width: 44px; height: 44px; border-color: var(--silver); border-width: 6px; }
  .card-back .brand-name { color: var(--silver); font-size: 44px; letter-spacing: 4px; }
</style>
</head>
<body>
<main class="canvas">
  <section class="card card-front" aria-label="Business card front">
    <div class="front-top">
      <span class="brand-mark" aria-hidden="true"></span>
      <span class="brand-name">Cedar Ridge Mechanical</span>
    </div>
    <div class="front-band"></div>
    <div class="front-bottom">
      <div class="identity">
        <p class="identity-name">FULL NAME</p>
        <p class="identity-role">POSITION</p>
      </div>
      <div class="divider"></div>
      <ul class="contact-list">
        <li>
          <svg viewBox="0 0 24 24" aria-hidden="true"><path d="M6.6 10.8a15.1 15.1 0 0 0 6.6 6.6l2.2-2.2c.3-.3.7-.4 1-.2 1.1.4 2.3.6 3.6.6.6 0 1 .4 1 1V20c0 .6-.4 1-1 1C10.6 21 3 13.4 3 4c0-.6.4-1 1-1h3.5c.6 0 1 .4 1 1 0 1.3.2 2.5.6 3.6.1.3 0 .7-.2 1z"/></svg>
          <span>(000) 000 0000</span>
        </li>
        <li>
          <svg viewBox="0 0 24 24" aria-hidden="true"><path d="M2 5h20v14H2zm2 2v.4l8 5.3 8-5.3V7zm0 2.8V17h16V9.8l-8 5.3z"/></svg>
          <span>email@company.com</span>
        </li>
        <li>
          <svg viewBox="0 0 24 24" aria-hidden="true"><path d="M12 2a10 10 0 1 0 0 20 10 10 0 0 0 0-20zm6.9 9h-3a15 15 0 0 0-1.3-6.1A8 8 0 0 1 18.9 11zM12 4c.9 1.2 1.8 3.6 1.9 7h-3.8c.1-3.4 1-5.8 1.9-7zM9.4 4.9A15 15 0 0 0 8.1 11h-3a8 8 0 0 1 4.3-6.1zM5.1 13h3a15 15 0 0 0 1.3 6.1A8 8 0 0 1 5.1 13zM12 20c-.9-1.2-1.8-3.6-1.9-7h3.8c-.1 3.4-1 5.8-1.9 7zm2.6-.9a15 15 0 0 0 1.3-6.1h3a8 8 0 0 1-4.3 6.1z"/></svg>
          <span>www.company.com</span>
        </li>
        <li>
          <svg viewBox="0 0 24 24" aria-hidden="true"><path d="M12 2a7 7 0 0 0-7 7c0 5.2 7 13 7 13s7-7.8 7-13a7 7 0 0 0-7-7zm0 9.5A2.5 2.5 0 1 1 12 6.5a2.5 2.5 0 0 1 0 5z"/></svg>
          <span>123 Name Street, 000<br>Your City, 00000-000</span>
        </li>
      </ul>
    </div>
  </section>

  <section class="card card-back" aria-label="Business card back">
    <span class="brand-mark" aria-hidden="true"></span>
    <span class="brand-name">Cedar Ridge Mechanical</span>
  </section>
</main>
</body>
</html>
```